Black Matte card with samurai logo which I would like it to be textured and company name on one side and on the other side I would like the company information with the reno (Face logo) Sushi logo. Double Sided card.

majority customers are University students, University sororities and fraternities.

It Company

Reno Sushi
317 W. Harlow Ave
Tucson, AZ 85042
Phone (520)413-6271
Fax (520)357-1846
E-mail: Renosushidesert@mailbox-example.com
FB: Renosushidesert
Twitter: Renosushidesert

• Present Normal

```html
<!DOCTYPE html>
<html lang="en">
<head>
<meta charset="utf-8">
<title>Reno Sushi – Business Card</title>
<link rel="stylesheet" href="https://fonts.googleapis.com/css2?family=Macondo&display=swap">
<style>
  :root {
    --page: #ffffff;
    --card: #070707;
    --accent: #e3141b;
    --ink: #f4f4f4;
    --font-main: "Macondo", "Papyrus", fantasy;
  }
  * { margin: 0; padding: 0; box-sizing: border-box; }
  html, body {
    width: 1200px;
    height: 702px;
    overflow: hidden;
    background: var(--page);
  }
  .card {
    position: absolute;
    left: 44px;
    top: 43px;
    width: 1111px;
    height: 616px;
    background: var(--card);
    font-family: var(--font-main);
    color: var(--ink);
  }
  .brand {
    position: absolute;
    left: 0;
    right: 0;
    top: 82px;
    display: flex;
    justify-content: center;
    align-items: center;
    gap: 20px;
  }
  .brand-mark {
    width: 44px;
    height: 44px;
    border-radius: 50%;
    background: var(--accent);
    flex: none;
  }
  .brand-name {
    font-size: 52px;
    font-weight: 400;
    line-height: 1;
    color: var(--ink);
  }
  .divider {
    position: absolute;
    left: 0;
    right: 0;
    top: 219px;
    height: 5px;
    background: var(--accent);
  }
  .company {
    position: absolute;
    left: 0;
    right: 0;
    top: 268px;
    text-align: center;
  }
  .company-name {
    font-size: 40px;
    font-weight: 400;
    line-height: 1.1;
  }
  .company-address {
    font-size: 24px;
    line-height: 1.4;
  }
  .contacts {
    position: absolute;
    left: 76px;
    top: 424px;
    list-style: none;
  }
  .contact {
    display: flex;
    align-items: center;
    height: 33px;
    font-size: 23px;
  }
  .contact-icon {
    width: 26px;
    height: 26px;
    margin-right: 14px;
    flex: none;
    fill: var(--ink);
  }
</style>
</head>
<body>
  <main class="card">
    <div class="brand">
      <span class="brand-mark" aria-hidden="true"></span>
      <span class="brand-name">Reno Sushi</span>
    </div>

    <div class="divider"></div>

    <section class="company">
      <h1 class="company-name">Reno Sushi</h1>
      <p class="company-address">317 W. Harlow Ave Tucson, AZ 85042</p>
    </section>

    <ul class="contacts">
      <li class="contact">
        <svg class="contact-icon" viewBox="0 0 24 24" aria-label="Phone">
          <path d="M6.6 2.5l3 4.2c.4.6.3 1.3-.2 1.8L8 9.8c1 2.4 3.1 4.6 5.6 5.7l1.3-1.4c.5-.5 1.3-.6 1.8-.2l4 2.9c.6.4.7 1.2.3 1.8l-1.4 2c-.6.8-1.6 1.1-2.5.8C10.7 19 5 13.3 2.6 6.6c-.3-.9 0-1.9.8-2.5l1.5-1.3c.5-.5 1.3-.5 1.7.1z"/>
        </svg>
        <span>(520)413-6271</span>
      </li>
      <li class="contact">
        <svg class="contact-icon" viewBox="0 0 24 24" aria-label="Fax">
          <rect x="1" y="8" width="4" height="15"/>
          <rect x="6" y="2" width="10" height="6"/>
          <path d="M6 8h17v15H6z M9 12v2h3v-2z M14 12v2h3v-2z M19 12v2h2v-2z M9 16v2h3v-2z M14 16v2h3v-2z M19 16v2h2v-2z" fill-rule="evenodd"/>
        </svg>
        <span>(520)357-1846</span>
      </li>
      <li class="contact">
        <svg class="contact-icon" viewBox="0 0 24 24" aria-label="Email">
          <path d="M1 5h22v2L12 14 1 7z M1 9.3l11 7 11-7V20H1z"/>
        </svg>
        <span>Renosushidesert@mailbox-example.com</span>
      </li>
      <li class="contact">
        <svg class="contact-icon" viewBox="0 0 24 24" aria-label="Social page">
          <path d="M3 3h18a1 1 0 0 1 1 1v12a1 1 0 0 1-1 1H10l-5 4v-4H3a1 1 0 0 1-1-1V4a1 1 0 0 1 1-1z"/>
        </svg>
        <span>Renosushidesert</span>
      </li>
      <li class="contact">
        <svg class="contact-icon" viewBox="0 0 24 24" aria-label="Social feed">
          <circle cx="18" cy="5" r="3.2"/>
          <circle cx="6" cy="12" r="3.2"/>
          <circle cx="18" cy="19" r="3.2"/>
          <path d="M17 4.2l1 1.8L7 12.9l-1-1.8z M6 12.9l1-1.8 11 6.9-1 1.8z"/>
        </svg>
        <span>Renosushidesert</span>
      </li>
    </ul>
  </main>
</body>
</html>
```